Meridale Bed Company Needs Business Card

Looking for a very nice looking business card. Creative but not extravagant. We sell beds and pillows across the U.S. and need something professional but catchy. I have attached the logo.

Name : Devin Holt
Title : President
Phone : (800) 471-2960
Email: sleep@quilmora.com
Website: www.quilmora.com

Can be single-sided or double-sided
horizontal or vertical

Can use Blues/Greys

Target Market(s)

Mass Market

Industry/Entity Type

Retail

Contact Information for Business Card

Name : Devin Holt
Title : President
Phone : (800) 471-2960
Email: sleep@quilmora.com
Website: www.quilmora.com

Requirements
Must have
• Clean, Modern, Smooth
• Can use Blues/Greys
• On the other side without the information - have something simple like www.quilmora.com or our logo
Nice to have
• Surprise me
Should not have
• Nothing crazy, nothing cluttered

```html
<!DOCTYPE html>
<html lang="en">
<head>
<meta charset="utf-8">
<title>Quilmora Business Card</title>
<link rel="stylesheet" href="https://fonts.googleapis.com/css2?family=Open+Sans:wght@300;400;700&display=swap">
<style>
  :root {
    --page-bg: #e6e8ea;
    --card-white: #ffffff;
    --card-white-shade: #f1f2f3;
    --brand-blue: #35a7dc;
    --band-blue-light: #33a6da;
    --band-blue-dark: #1d8fc8;
    --divider-grey: #6f7376;
    --back-grey-light: #5e5f61;
    --back-grey-dark: #3f4042;
    --back-url: #a9abad;
    --name-ink: #3c6784;
    --title-ink: #4f7a96;
    --contact-ink: #ffffff;
  }
  * { margin: 0; padding: 0; box-sizing: border-box; }
  html, body { width: 1200px; height: 843px; overflow: hidden; }
  body {
    background: var(--page-bg);
    font-family: "Open Sans", Arial, sans-serif;
    position: relative;
  }
  .card {
    position: absolute;
    left: 290px;
    width: 620px;
    height: 354px;
    overflow: hidden;
    box-shadow: 0 6px 18px rgba(0,0,0,0.18);
  }
  .card-back {
    top: 50px;
    background: linear-gradient(160deg, var(--back-grey-light), var(--back-grey-dark));
  }
  .card-front {
    top: 439px;
    background: linear-gradient(180deg, var(--card-white), var(--card-white-shade));
  }
  .wordmark {
    position: absolute;
    font-weight: 300;
    letter-spacing: 2px;
    line-height: 1;
  }
  .card-back .wordmark {
    color: var(--card-white);
    font-size: 84px;
    left: 0; right: 0;
    top: 112px;
    text-align: center;
  }
  .back-url {
    position: absolute;
    left: 0; right: 0;
    top: 236px;
    text-align: center;
    color: var(--back-url);
    font-size: 11px;
    letter-spacing: 6px;
  }
  .card-front .wordmark {
    color: var(--brand-blue);
    font-size: 80px;
    left: 200px;
    top: 62px;
  }
  .info-band {
    position: absolute;
    left: 0; top: 0;
    width: 620px; height: 354px;
  }
  .contact-list {
    position: absolute;
    left: 34px;
    top: 222px;
    list-style: none;
    color: var(--contact-ink);
    font-size: 14px;
    line-height: 22px;
  }
  .contact-list li { display: flex; align-items: center; gap: 9px; }
  .contact-list svg { width: 13px; height: 13px; flex: none; }
  .person {
    position: absolute;
    right: 34px;
    top: 278px;
    text-align: right;
  }
  .person-name {
    color: var(--name-ink);
    font-weight: 700;
    font-size: 19px;
    line-height: 24px;
  }
  .person-title {
    color: var(--title-ink);
    font-size: 15px;
    line-height: 20px;
  }
</style>
</head>
<body>

  <section class="card card-back" aria-label="Card back">
    <div class="wordmark">quilmora</div>
    <div class="back-url">www.quilmora.com</div>
  </section>

  <section class="card card-front" aria-label="Card front">
    <div class="wordmark">quilmora</div>

    <svg class="info-band" viewBox="0 0 620 354" aria-hidden="true">
      <defs>
        <linearGradient id="bandFill" x1="0" y1="0" x2="1" y2="1">
          <stop offset="0" stop-color="var(--band-blue-light)"/>
          <stop offset="1" stop-color="var(--band-blue-dark)"/>
        </linearGradient>
      </defs>
      <path d="M0 192 H462 L471 201 L480 192 H620 V354 H0 Z" fill="url(#bandFill)"/>
      <path d="M0 189.5 H461 L471 199.5 L481 189.5 H620" fill="none" stroke="var(--divider-grey)" stroke-width="3"/>
    </svg>

    <ul class="contact-list">
      <li>
        <svg viewBox="0 0 16 16"><path fill="currentColor" d="M3 2h3l1.5 3.5-2 1.3a9 9 0 0 0 3.7 3.7l1.3-2L14 10v3a1.5 1.5 0 0 1-1.5 1.5C7 14.5 1.5 9 1.5 3.5A1.5 1.5 0 0 1 3 2z"/></svg>
        (800) 471-2960
      </li>
      <li>
        <svg viewBox="0 0 16 16"><rect x="1" y="3" width="14" height="10" rx="1" fill="currentColor"/><path d="M1.5 3.8 8 9l6.5-5.2" fill="none" stroke="#2a9bd2" stroke-width="1.3"/></svg>
        sleep@quilmora.com
      </li>
      <li>
        <svg viewBox="0 0 16 16"><circle cx="8" cy="8" r="6.5" fill="none" stroke="currentColor" stroke-width="1.6"/><path d="M1.5 8h13M8 1.5c-2.5 3-2.5 10 0 13M8 1.5c2.5 3 2.5 10 0 13" fill="none" stroke="currentColor" stroke-width="1.2"/></svg>
        www.quilmora.com
      </li>
    </ul>

    <div class="person">
      <div class="person-name">Devin Holt</div>
      <div class="person-title">President</div>
    </div>
  </section>

</body>
</html>
```